Construction company business card

One side to be the logo with the company name, The other side I would like: (Tomas verbick) Project manager 41 barrow crescent hallam 52917306224783(03) 9703 2428Info@gudeljgroup.comAnd then maybe a couple dot points saying what we do:Construction (commercial & industrial) Civil construction

Anything else please contact me!
Maybe curved st one edge of the card

Target Market(s)

Older clientele

Industry/Entity Type

Construction Company

Contact Information for Business Card

Read above

Colors
3277b5
1b1b1b
9d9d9d

Requirements
Must have
• Use my logo on one side
Nice to have
• Read above
Should not have
• Read above

```html
<!DOCTYPE html>
<html lang="en">
<head>
<meta charset="utf-8">
<title>Stonereach Property Group – Business Card</title>
<link href="https://fonts.googleapis.com/css2?family=Lato:wght@400;700&display=swap" rel="stylesheet">
<style>
  :root {
    --brand-blue: #3277b5;
    --ink: #1b1b1b;
    --steel: #9d9d9d;
    --paper: #ffffff;
    --backdrop: #d9d9d9;
    --rule: #5a92c6;
  }
  * { margin: 0; padding: 0; box-sizing: border-box; }
  html, body {
    width: 1200px; height: 802px; overflow: hidden;
    background: var(--backdrop);
    font-family: "Lato", sans-serif;
  }
  .canvas { position: relative; width: 1200px; height: 802px; }
  .card {
    position: absolute; top: 274px;
    width: 442px; height: 264px;
    background: var(--paper); overflow: hidden;
  }
  .card--contact { left: 136px; }
  .card--brand { left: 624px; }

  .contact-panel { position: absolute; inset: 0; }

  .contact-text {
    position: absolute; right: 23px; top: 36px;
    text-align: right; color: var(--paper);
  }
  .person-name {
    font-size: 16px; font-weight: 700; text-transform: uppercase;
    letter-spacing: 0.1px; line-height: 18px;
  }
  .person-role { font-size: 12px; line-height: 14px; }
  .contact-list { list-style: none; margin-top: 10px; }
  .contact-list li {
    font-size: 12px; line-height: 16px;
    display: flex; justify-content: flex-end; align-items: center; gap: 3px;
  }
  .contact-list svg { width: 10px; height: 10px; fill: var(--paper); }
  .address { margin-top: 7px; font-size: 12px; line-height: 16px; }
  .address-line { display: flex; justify-content: flex-end; align-items: center; gap: 4px; }
  .address-line svg { width: 9px; height: 11px; fill: var(--paper); }
  .address-town { padding-right: 13px; }

  .divider {
    position: absolute; left: 263px; right: 23px; top: 175px;
    height: 1px; background: var(--rule);
  }
  .services {
    position: absolute; right: 23px; top: 185px;
    list-style: none; text-align: right; color: var(--paper);
    font-size: 12px; line-height: 16px;
  }
  .services .dot::after {
    content: ""; display: inline-block; width: 7px; height: 7px;
    border-radius: 50%; background: var(--paper); margin-left: 3px;
  }
  .services .sub { padding-right: 10px; }

  .brand-lockup {
    position: absolute; left: 0; right: 0; top: 55px;
    display: flex; flex-direction: column; align-items: center; gap: 14px;
  }
  .brand-dot { width: 84px; height: 84px; border-radius: 50%; background: var(--brand-blue); }
  .brand-name {
    font-size: 20px; font-weight: 700; color: var(--brand-blue);
    letter-spacing: 0.5px;
  }
</style>
</head>
<body>
<main class="canvas">
  <section class="card card--contact">
    <svg class="contact-panel" viewBox="0 0 442 264" aria-hidden="true">
      <path d="M130 0 H442 V264 H125 C40 240 0 170 2 120 C4 60 60 8 130 0 Z" fill="var(--brand-blue)"/>
    </svg>
    <div class="contact-text">
      <p class="person-name">Tomas Verbick</p>
      <p class="person-role">Project manager</p>
      <ul class="contact-list">
        <li>7306224783
          <svg viewBox="0 0 10 10"><path d="M1 2 C1 1 2 1 3 1 L4 3 L3 4 C4 5 5 6 6 7 L7 6 L9 7 C9 8 9 9 8 9 C4 9 1 6 1 2 Z"/></svg>
        </li>
        <li>(03) 9418 6573
          <svg viewBox="0 0 10 10"><path d="M2.5 0.5 H7.5 V9.5 H2.5 Z M3.5 1.5 V7.5 H6.5 V1.5 Z"/></svg>
        </li>
        <li>Info@verbickgroup.com
          <svg viewBox="0 0 10 10"><path d="M0.5 2 H9.5 V8 H0.5 Z M1.2 2.6 L5 5.4 L8.8 2.6 Z"/></svg>
        </li>
      </ul>
      <div class="address">
        <p class="address-line">41 barrow crescent
          <svg viewBox="0 0 9 11"><path d="M4.5 0.5 C2.3 0.5 0.8 2 0.8 4 C0.8 6.5 4.5 10.5 4.5 10.5 C4.5 10.5 8.2 6.5 8.2 4 C8.2 2 6.7 0.5 4.5 0.5 Z M4.5 2.5 A1.5 1.5 0 1 1 4.49 2.5 Z"/></svg>
        </p>
        <p class="address-town">kerrowvale 5291</p>
      </div>
    </div>
    <div class="divider"></div>
    <ul class="services">
      <li class="dot">Construction</li>
      <li class="sub">(commercial &amp; industrial)</li>
      <li class="dot">Civil construction</li>
    </ul>
  </section>

  <section class="card card--brand">
    <div class="brand-lockup">
      <div class="brand-dot"></div>
      <p class="brand-name">Stonereach Property Group</p>
    </div>
  </section>
</main>
</body>
</html>
```